Animal Horse & Bedding Company Needs a Website Coded & Designed

We need a website for a new animal bedding and feed company that is visually grabbing and vibrant. We would like to see a website that displays trust, quality and confidence. Needs to be responsive and mobile friendly for all browsers and coded for both Android & IOS. SEO is also important.

Joomla or Wordpress – must be both desktop and mobile friendly with fast page load speed. Need the ability to edit ourselves in Wordpress or Joomla.

Full details attached below with some layout and content ideas.

Coding

Coded - Design and coding required

Number of Pages Required

5+ page

Font styles to use
Sans Serif

Requirements
Must have
• Needs to be responsive and mobile friendly for all browsers and coded for both Android & IOS. SEO is also important.

Wordpress – must be both desktop and mobile friendly with fast page load speed. Need the ability to edit ourselves in Wordpress.

Logo Colours:
Dark Brown
CMYK: 50 / 70 / 80 / 70
Pantone: 4625C

Orange
CMYK: 0 / 50 / 100 / 0
Pantone: 144C
Nice to have
• Use picture of building attached and super impose logo on building.

```html
<!DOCTYPE html>
<html lang="en">
<head>
<meta charset="utf-8">
<title>Golden Bale – Bedding &amp; Feed</title>
<link href="https://fonts.googleapis.com/css2?family=Montserrat:wght@300;400;500;600;700&display=swap" rel="stylesheet">
<style>
:root{
  --orange:#f7941d;
  --orange-soft:#f9a84a;
  --ink:#1b1b1b;
  --text:#7a7a7a;
  --muted:#9a9a9a;
  --line:#e4e4e4;
  --band:#f5f5f5;
  --white:#ffffff;
}
*{box-sizing:border-box;margin:0;padding:0}
html,body{width:1200px;height:3576px;overflow:hidden}
body{font-family:'Montserrat',sans-serif;color:var(--ink);background:var(--white);position:relative}
.abs{position:absolute}
.btn{display:inline-block;background:var(--orange);color:#fff;font-weight:600;font-size:12px;padding:0 16px;height:27px;line-height:27px;border-radius:2px}
/* header */
.header{position:absolute;left:0;top:0;width:1200px;height:62px;background:#fff}
.brand{left:172px;top:12px;display:flex;align-items:center;gap:8px}
.brand-dot{width:26px;height:26px;border-radius:50%;background:var(--orange)}
.brand-name{font-weight:700;font-size:18px;letter-spacing:1px;color:var(--ink)}
.nav{left:546px;top:0;height:62px;display:flex;align-items:center;gap:32px;font-size:13px}
.nav a{color:var(--ink);text-decoration:none}
.nav .active{color:var(--orange);position:relative}
.nav .active::after{content:"";position:absolute;left:8px;right:8px;bottom:-10px;height:2px;background:var(--orange)}
.nav-cta{left:922px;top:17px;height:29px;line-height:29px;width:105px;text-align:center;padding:0}
/* hero */
.hero{left:0;top:62px;width:1200px;height:491px;background:linear-gradient(120deg,#4f5a2c 0%,#6b6a3a 35%,#5a3b24 60%,#8a6a56 85%,#a07a70 100%)}
.hero-title{left:172px;top:114px;font-size:45px;line-height:43px;font-weight:700;color:#fff}
.hero-sub{left:172px;top:268px;width:310px;font-size:14.5px;line-height:16px;color:#fff}
.hero .btn{left:172px;top:344px;position:absolute}
/* features */
.features{left:0;top:553px;width:1200px;height:249px;background:var(--band)}
.feature{position:absolute;top:62px;width:240px;text-align:center}
.feature h3{font-size:14.5px;font-weight:600;margin-top:14px}
.feature p{font-size:9.5px;color:var(--muted);line-height:12px;margin-top:4px}
.divider{position:absolute;top:86px;width:1px;height:80px;background:var(--line)}
/* photo blocks */
.photo{position:absolute;border-radius:4px}
.section-text p{font-size:9.8px;line-height:14.5px;color:var(--text);margin-bottom:14px}
.kicker{font-size:16px;color:#555;font-weight:400}
h2{font-size:25px;font-weight:700;letter-spacing:-.3px}
.list{list-style:none;font-size:9.8px;color:var(--text)}
.list li{height:20px;display:flex;align-items:center;gap:15px}
.list li::before{content:"›";color:var(--orange);font-size:13px;width:7px}
/* products */
.card{position:absolute;top:2460px;width:198px;height:271px;border:1px solid var(--line);border-radius:6px;background:#fff;text-align:center}
.bag{position:absolute;left:55px;top:32px;width:88px;height:92px;border-radius:6px;background:linear-gradient(180deg,#e9e9e9,#cfcfcf 60%,#8b6a45 61%,#6e4f30)}
.card .name{position:absolute;top:182px;width:100%;font-size:14.5px;font-weight:500}
.stars{position:absolute;top:204px;width:100%;display:flex;justify-content:center;gap:2px}
.card .price{position:absolute;top:229px;width:100%;font-size:15px;font-weight:600}
.card.featured .inner{position:absolute;left:15px;top:15px;width:168px;height:241px;background:var(--orange-soft);border-radius:6px}
.card.featured .name,.card.featured .price{color:#f7c48a}
.arrow{position:absolute;color:#c8c8c8;font-size:20px}
/* testimonial */
.testimonial{left:0;top:2835px;width:1200px;height:419px;background:radial-gradient(ellipse at 60% 60%,#5a4a34 0%,#3a3126 45%,#2a241c 100%)}
.testimonial .center{position:absolute;left:0;width:1200px;text-align:center;color:#fff}
.dots{position:absolute;left:579px;top:310px;display:flex;gap:6px}
.dots span{width:9px;height:9px;border:1px solid #fff;border-radius:50%}
.dots span.on{background:#fff}
/* footer */
.footer h4{position:absolute;top:3337px;font-size:14.5px;font-weight:600}
.footer .col{position:absolute;font-size:9px;color:var(--muted);line-height:21px}
.social{position:absolute;left:830px;top:3375px;display:flex;gap:12px}
.social span{width:9px;height:9px;border-radius:50%;background:#8a8a8a}
.social span:nth-child(2){background:var(--orange)}
.email{position:absolute;left:830px;top:3410px;width:197px;height:28px;border:1px solid #eee;font-size:8.5px;color:#bbb;line-height:28px;padding-left:30px}
.email::before{content:"";position:absolute;left:10px;top:10px;width:9px;height:8px;border-radius:2px;background:var(--orange)}
.subscribe{position:absolute;left:830px;top:3443px;width:197px;height:28px;background:var(--orange);color:#fff;font-size:9px;text-align:center;line-height:28px;border-radius:2px}
.copyright{position:absolute;left:0;top:3524px;width:1200px;border-top:1px solid var(--line);text-align:center;font-size:9px;color:#555;padding-top:14px}
</style>
</head>
<body>

<header class="header">
  <div class="abs brand"><span class="brand-dot"></span><span class="brand-name">GOLDEN BALE</span></div>
  <nav class="abs nav">
    <a class="active" href="#">Home</a><a href="#">About Us</a><a href="#">Feed</a><a href="#">Bedding</a><a href="#">Contact</a>
  </nav>
  <a class="abs btn nav-cta">Get a Quote</a>
</header>

<section class="abs hero" role="img" aria-label="Dark bay horse trotting in a fenced paddock with a small dog, green trees behind">
  <h1 class="abs hero-title" style="top:114px">Best Bedding<br>and Feed for<br>your Horse</h1>
  <p class="abs hero-sub">Golden Bale offers supply and delivery of fresh bedding as well as removal of waste bedding.</p>
  <a class="btn">Get a Quote</a>
</section>

<section class="abs features">
  <div class="feature" style="left:186px">
    <svg width="52" height="62" viewBox="0 0 52 62"><path d="M14 38 8 60l10-5 6 7 4-20zM38 38l6 22-10-5-6 7-4-20z" fill="#f7941d"/><circle cx="26" cy="26" r="24" fill="#f7941d"/><circle cx="26" cy="26" r="15" fill="none" stroke="#fff" stroke-width="3"/><path d="M19 26l5 5 9-10" fill="none" stroke="#fff" stroke-width="3"/></svg>
    <h3>Quality Guaraanteed</h3>
    <p>Grown for quality 100% natural with<br>no chemicals or additives.</p>
  </div>
  <div class="divider" style="left:443px"></div>
  <div class="feature" style="left:480px">
    <svg width="56" height="62" viewBox="0 0 56 56" style="margin-top:2px"><g fill="#f7941d"><circle cx="28" cy="28" r="20"/><rect x="23" y="0" width="10" height="12"/><rect x="23" y="44" width="10" height="12"/><rect x="0" y="23" width="12" height="10"/><rect x="44" y="23" width="12" height="10"/><rect x="23" y="0" width="10" height="12" transform="rotate(45 28 28)"/><rect x="23" y="44" width="10" height="12" transform="rotate(45 28 28)"/><rect x="0" y="23" width="12" height="10" transform="rotate(45 28 28)"/><rect x="44" y="23" width="12" height="10" transform="rotate(45 28 28)"/></g><circle cx="28" cy="28" r="9" fill="#f5f5f5"/></svg>
    <h3>Full Service Solution</h3>
    <p>Dedicated in providing a full service solution<br>of bedding supply &amp; waste removal.</p>
  </div>
  <div class="divider" style="left:747px"></div>
  <div class="feature" style="left:773px">
    <svg width="60" height="62" viewBox="0 0 60 62"><rect x="14" y="2" width="16" height="8" rx="2" fill="#f7941d"/><path d="M16 12h12c10 8 14 18 14 28 0 12-8 20-20 20S2 52 2 40c0-10 4-20 14-28z" fill="#f7941d"/><text x="22" y="46" font-size="20" font-weight="700" fill="#fff" text-anchor="middle" font-family="Montserrat,sans-serif">$</text><g fill="#f7941d"><rect x="40" y="30" width="18" height="6" rx="2"/><rect x="40" y="40" width="18" height="6" rx="2"/><rect x="40" y="50" width="18" height="6" rx="2"/></g></svg>
    <h3>Convenient &amp; Cost Effective</h3>
    <p>Compressed bags, pellets or bulk products<br>saving in shipping cost.</p>
  </div>
</section>

<div class="photo" style="left:172px;top:906px;width:366px;height:365px;background:linear-gradient(180deg,#b9b6a8 0%,#8e8a78 40%,#2e2e2e 60%,#8f7e5e 100%)" role="img" aria-label="Dairy cows feeding on hay inside an open barn"></div>
<div class="abs section-text" style="left:588px;top:938px;width:440px">
  <div class="kicker">Welcome to</div>
  <h2 style="margin:2px 0 18px">Golden Bale</h2>
  <p>Golden Bale is a locally owned company located in Millbrook, AB. We are dedicated in providing high quality products and services. Producing, buying and marketing hay and straw for x amount of years. Insert blurb on ownership/history of key staff/owners.</p>
  <p>Golden Bale offers supply and delivery of fresh bedding as well as removal of waste bedding. Let us deliver you a container of fresh straw and haul your waste bedding away. A full service solution that is sustainable and responsible.</p>
  <p>Your animal deserves the very best in health and comfort to keep them healthy, strong and happy. Our products are designed for horses, livestock (goats, cattle and sheep), small caged animals (rabbits, guinea pigs and more).</p>
  <a class="btn" style="margin-top:4px;width:98px;text-align:center;padding:0">Get A Quote</a>
</div>

<section class="abs" style="left:0;top:1368px;width:1200px;height:572px;background:var(--band)">
  <div class="abs section-text" style="left:172px;top:110px;width:426px">
    <h2 style="margin-bottom:8px">Clean, dry, natural solution</h2>
    <p style="margin:0">For many people, their animals, whether it be a horse, goat or other are more than just an animal, they are a part of your family, a way of life, and their comfort is important. Fine cut 100% chopped straw offers a softer bedding for your equine or other large and/or small animal.</p>
    <p>This straw bedding is light weight which allows for easier spreading, removing and hauling away. Straw also decomposes a lot faster than wood shavings and makes for great compost material.</p>
    <ul class="list">
      <li>100% Natural Chopped Straw</li><li>Low Dust</li><li>Chemical &amp; Additive Free</li><li>Clean &amp; Highly Absorbent</li><li>Cheaper than Wood Shavings</li><li>Economic – less used and less wasted</li><li>Environmentally Friendly – Recyclable &amp; Compostable</li>
    </ul>
    <a class="btn" style="margin-top:32px;width:98px;text-align:center;padding:0">Get A Quote</a>
  </div>
  <div class="photo" style="left:661px;top:103px;width:366px;height:367px;background:linear-gradient(180deg,#7a4a22 0%,#b36a2e 35%,#9a7a5e 55%,#8a6a52 100%)" role="img" aria-label="Indoor riding arena with wooden roof beams and a dirt floor"></div>
</section>

<div class="photo" style="left:172px;top:2043px;width:366px;height:366px;background:linear-gradient(135deg,#8a8e94 0%,#d8d4cc 40%,#7a5a44 70%,#5a3e2c 100%)" role="img" aria-label="Row of white goats feeding through a pen fence"></div>
<div class="abs section-text" style="left:588px;top:2058px;width:440px">
  <h2 style="margin-bottom:8px">Our Feed</h2>
  <p>Hay cubes and pellets are made from premium hay offering a variety of animals a feed that is non-GMO and packed with natural nutrients. These pellets and cubes are less bulky to handle, store and ship. As well, they reduce the amount of wasted feed.</p>
  <ul class="list">
    <li>100% Natural</li><li>Chemical &amp; Additive Free</li><li>Available in Pellets or Cubes</li><li>High Protein Content</li><li>Eliminate Waste In Feeding</li><li>Clean - Eliminates Dust From Feeding Baled Hay</li><li>Cost Effective</li><li>Convenient</li><li>Less wasted feed</li>
  </ul>
  <a class="btn" style="margin-top:26px;width:98px;text-align:center;padding:0">Get A Quote</a>
</div>

<span class="arrow" style="left:110px;top:2582px">‹</span>
<div class="card" style="left:172px"><div class="bag" role="img" aria-label="Feed bag with pellets"></div><div class="name">Product Name</div><div class="stars"><svg width="68" height="11" viewBox="0 0 68 11"><g fill="#f7a21d"><path id="s" d="M5.5 0l1.6 3.6 3.9.3-3 2.5.9 3.8-3.4-2-3.4 2 .9-3.8-3-2.5 3.9-.3z"/><use href="#s" x="14"/><use href="#s" x="28"/><use href="#s" x="42"/><use href="#s" x="56"/></g></svg></div><div class="price">$100.00</div></div>
<div class="card" style="left:390px"><div class="bag" role="img" aria-label="Feed bag with pellets"></div><div class="name">Product Name</div><div class="stars"><svg width="68" height="11" viewBox="0 0 68 11"><g fill="#f7a21d"><use href="#s"/><use href="#s" x="14"/><use href="#s" x="28"/><use href="#s" x="42"/><use href="#s" x="56"/></g></svg></div><div class="price">$100.00</div></div>
<div class="card featured" style="left:612px"><div class="inner"></div><div class="bag" style="opacity:.25" role="img" aria-label="Feed bag with pellets"></div>
  <svg class="abs" style="left:71px;top:105px" width="56" height="56" viewBox="0 0 56 56"><circle cx="28" cy="28" r="28" fill="#fff"/><circle cx="26" cy="26" r="9" fill="none" stroke="#f7941d" stroke-width="2.5"/><path d="M32.5 32.5l7 7M22 26h8M26 22v8" stroke="#f7941d" stroke-width="2.5"/></svg>
  <div class="name">Product Name</div><div class="stars"><svg width="68" height="11" viewBox="0 0 68 11"><g fill="#f7b56a"><use href="#s"/><use href="#s" x="14"/><use href="#s" x="28"/><use href="#s" x="42"/><use href="#s" x="56"/></g></svg></div><div class="price">$100.00</div></div>
<div class="card" style="left:830px"><div class="bag" role="img" aria-label="Feed bag with pellets"></div><div class="name">Product Name</div><div class="stars"><svg width="68" height="11" viewBox="0 0 68 11"><g fill="#f7a21d"><use href="#s"/><use href="#s" x="14"/><use href="#s" x="28"/><use href="#s" x="42"/><use href="#s" x="56"/></g></svg></div><div class="price">$100.00</div></div>
<span class="arrow" style="left:1078px;top:2582px">›</span>

<section class="abs testimonial" role="img" aria-label="Young lambs standing in soft evening light">
  <h2 class="center" style="top:108px">Whats Our Clients Says</h2>
  <div class="center" style="top:163px;font-size:14.5px;font-weight:500">Daniel Marsh</div>
  <div class="center" style="top:184px;font-size:9.5px">Managing Member, Northfield Holdings</div>
  <p class="center" style="top:218px;font-size:9.8px;line-height:15px;left:355px;width:490px">Lorem Ipsum is simply dummy text of the printing and typesetting industry. Lorem Ipsum has been the industry's standard dummy text ever since the 1500s, when an unknown printer took a galley of type and scrambled it to make a type specimen book. It has survived not only five centuries, but also the leap into electronic typesetting, remaining essentially unchanged.</p>
  <span class="abs" style="left:246px;top:250px;color:#fff;font-size:20px">‹</span>
  <span class="abs" style="left:944px;top:250px;color:#fff;font-size:20px">›</span>
  <div class="dots"><span></span><span></span><span class="on"></span></div>
</section>

<footer class="footer">
  <div class="abs" style="left:172px;top:3370px;display:flex;align-items:center;gap:8px"><span class="brand-dot" style="width:22px;height:22px"></span><span class="brand-name" style="font-size:16px">GOLDEN BALE</span></div>
  <p class="col" style="left:172px;top:3453px;width:160px;line-height:11px">Ready to start a new project or curious about our process? Drop us a note or give us a call. We are happy to answer any questions and provide a free consultation.</p>
  <h4 style="left:433px">Menu</h4>
  <div class="col" style="left:435px;top:3370px">Home<br>About us<br>Feed<br>Badding<br>Contact</div>
  <h4 style="left:604px">Contact Us</h4>
  <div class="col" style="left:604px;top:3372px;line-height:12px;width:120px">Golden Bale<br>18 Orchard Lane #12, Fairview,<br>MA 01999<br><span style="display:block;margin-top:9px">555-014-2287</span><span style="display:block;margin-top:9px">hello@goldenbale.com</span></div>
  <h4 style="left:830px">Social Media</h4>
  <div class="social"><span></span><span></span><span></span><span></span><span></span></div>
  <div class="email">Email Address</div>
  <div class="subscribe">Subscribe Now</div>
  <div class="copyright">©2021 goldenbale. All Rights Reserved.</div>
</footer>

</body>
</html>
```